Business Card for a Jewellery Brand

Business card for an upscale jewellery brand. Attached is the brand logo and icon and color board. I am looking for two card versions: one for the founder and one is generic. The card should be elegant and convey upscale and premium feel. I am open to both square and rectangle card shapes.

Industry/Entity Type

Jewelry

Contact Information for Business Card

Two cards: (1) Sunela Parvaniya (Founder) (2) General
(1) Sunela Parvaniya card should have Name: Sunela Parvaniya, Title: Founder Email id: sunela@quiremo.com.au. Phone no: +61452913307
(2) Generic card should have Email id: info@quiremo.com.au. Phone no: +61436207518

Requirements
Must have
• Workmark
• ICON
• Phone no
• Email ID
• ABN: 58219740312 (Note: ABN is Business number in Australia)
• Website: www.quiremo.com.au
• Instagram: quiremo_jewellery
• Facebook: @quiremojewellery
Nice to have
• Tagline

```html
<!DOCTYPE html>
<html lang="en">
<head>
<meta charset="utf-8">
<title>Quiremo – Business Cards</title>
<link href="https://fonts.googleapis.com/css2?family=Josefin+Sans:wght@300;400&family=Open+Sans:wght@400;600&display=swap" rel="stylesheet">
<style>
  :root {
    --blush: #d48a8a;
    --blush-dark: #c97a7a;
    --paper: #fbfbfa;
    --ink: #555555;
    --rule: #9a9a9a;
    --stage: #e9e7e6;
    --white: #ffffff;
  }
  * { box-sizing: border-box; margin: 0; padding: 0; }
  html, body { width: 1200px; height: 900px; overflow: hidden; }
  body {
    background: var(--stage);
    font-family: "Open Sans", Arial, sans-serif;
    position: relative;
  }
  .card {
    position: absolute;
    left: 285px;
    width: 630px;
    height: 360px;
    box-shadow: 0 6px 18px rgba(0,0,0,0.12);
    overflow: hidden;
  }

  /* Front */
  .card-front { top: 60px; background: var(--blush); color: var(--white); }
  .front-brand {
    position: absolute; top: 92px; left: 0; width: 100%;
    display: flex; flex-direction: column; align-items: center; gap: 18px;
  }
  .brand-mark {
    width: 56px; height: 56px;
    border: 2px solid currentColor;
  }
  .wordmark {
    font-family: "Josefin Sans", Arial, sans-serif;
    font-weight: 300;
    font-size: 46px;
    letter-spacing: 14px;
    padding-left: 14px;
    line-height: 1;
  }
  .tagline-row {
    position: absolute; top: 262px; left: 60px; right: 60px;
    display: flex; align-items: center; gap: 14px;
  }
  .tagline-row .rule { flex: 1; height: 1px; background: rgba(255,255,255,0.75); }
  .tagline {
    font-family: "Josefin Sans", Arial, sans-serif;
    font-weight: 400; font-size: 13px; letter-spacing: 1.5px;
  }

  /* Back */
  .card-back { top: 480px; background: var(--paper); color: var(--ink); }
  .back-band {
    position: absolute; left: 0; right: 0; bottom: 0; height: 12px;
    background: var(--blush);
  }
  .back-brand {
    position: absolute; top: 36px; right: 40px;
    display: flex; flex-direction: column; align-items: center; gap: 14px;
    color: var(--blush);
  }
  .back-brand .brand-mark { width: 44px; height: 44px; }
  .back-brand .wordmark { font-size: 32px; letter-spacing: 10px; padding-left: 10px; }
  .back-rule {
    position: absolute; top: 160px; left: 40px; right: 40px;
    height: 1px; background: var(--rule);
  }
  .business-ids {
    position: absolute; top: 176px; right: 40px;
    text-align: right; font-size: 13px; line-height: 1.5;
  }
  .person {
    position: absolute; left: 40px; top: 196px;
  }
  .person-name { color: var(--blush-dark); font-weight: 600; font-size: 16px; }
  .person-title { font-size: 15px; margin-bottom: 8px; }
  .contact-list { list-style: none; font-size: 13px; line-height: 1.55; }
  .contact-list li { display: flex; align-items: center; gap: 10px; }
  .contact-list svg { width: 12px; height: 12px; flex: none; }
</style>
</head>
<body>

<section class="card card-front" aria-label="Card front">
  <div class="front-brand">
    <div class="brand-mark" aria-hidden="true"></div>
    <div class="wordmark">QUIREMO</div>
  </div>
  <div class="tagline-row">
    <span class="rule"></span>
    <span class="tagline">LOVE IS IN THE AIR</span>
    <span class="rule"></span>
  </div>
</section>

<section class="card card-back" aria-label="Card back">
  <div class="back-brand">
    <div class="brand-mark" aria-hidden="true"></div>
    <div class="wordmark">QUIREMO</div>
  </div>
  <div class="back-rule"></div>
  <div class="business-ids">
    <p>ABN: 58219740312</p>
    <p>www.quiremo.com.au</p>
  </div>
  <div class="person">
    <p class="person-name">Sunela Parvaniya</p>
    <p class="person-title">Founder</p>
    <ul class="contact-list">
      <li>
        <svg viewBox="0 0 12 12" aria-hidden="true"><rect x="2.5" y="0.5" width="7" height="11" rx="1.2" fill="none" stroke="#d48a8a" stroke-width="1.2"/><rect x="5" y="9" width="2" height="1" fill="#d48a8a"/></svg>
        +61452913307
      </li>
      <li>
        <svg viewBox="0 0 12 12" aria-hidden="true"><rect x="0.5" y="2" width="11" height="8" fill="#d48a8a"/><path d="M0.5 2 L6 6.5 L11.5 2" fill="none" stroke="#fff" stroke-width="1"/></svg>
        sunela@quiremo.com.au
      </li>
      <li>
        <svg viewBox="0 0 12 12" aria-hidden="true"><rect x="0.5" y="0.5" width="11" height="11" fill="#d48a8a"/></svg>
        quiremo_jewellery
      </li>
      <li>
        <svg viewBox="0 0 12 12" aria-hidden="true"><rect x="0.5" y="0.5" width="11" height="11" fill="#d48a8a"/></svg>
        @quiremojewellery
      </li>
    </ul>
  </div>
  <div class="back-band"></div>
</section>

</body>
</html>
```